tallow-brook.com

We are a small dollar lending company that will revolutionize the industry. We will do this by being completely transparent, fee free, etc and an interest rate that normal people can afford to pay. Over 10X less than our competition. We only allow our members to pay bills " bills paid fast", within 72 hours. Payday loans typically charge from 390%-600% with a terrible payback structure. We charge 36%, period, with a payback structure over 12 months. Our site will be very simple and easy to use but elegant at the same time. We do not want the site to be too busy, less is more and easier. We will have; Home, The Story, Why tallowbrook.com, Are you eligible? Members, Clients. To become a member you have to be referred by a current client of tallowbrook.com. A lot of the busy stuff will be saved for the Members and Clients sections. The feel must be elegant, easy to use and very simple to understand. I am looking for the green, white and black combinations of colors, very similar to my logo that was designed by Fernquillo.

```html
<!DOCTYPE html>
<html lang="en">
<head>
<meta charset="utf-8">
<title>tallow-brook.com</title>
<link rel="stylesheet" href="https://fonts.googleapis.com/css2?family=Arimo:wght@400&display=swap">
<style>
  :root {
    --green: #8dc63f;
    --white: #ffffff;
    --ink: #1a1a1a;
  }
  * { margin: 0; padding: 0; box-sizing: border-box; }
  html, body { width: 1200px; height: 821px; overflow: hidden; background: var(--white); }
  body { font-family: "Arimo", Arial, sans-serif; }
  .page { position: relative; width: 1200px; height: 821px; overflow: hidden; }

  .feature-art {
    position: absolute; left: 600px; top: 0;
    width: 600px; height: 821px;
    background: var(--green);
  }

  .brand {
    position: absolute; left: 348px; top: 100px;
    display: flex; align-items: center; gap: 8px;
    color: var(--ink); font-size: 18px; letter-spacing: 0.5px;
  }
  .brand-dot { width: 26px; height: 26px; border-radius: 50%; background: var(--green); }

  .main-nav a {
    position: absolute; transform: translate(-50%, -50%);
    white-space: nowrap; text-decoration: none;
    font-size: 19px; color: var(--ink); letter-spacing: 0.2px;
  }
  .main-nav a.is-active { color: var(--green); }

  .benefits {
    position: absolute; left: 826px; top: 233px; list-style: none;
    color: var(--white); font-size: 15.5px; letter-spacing: 0.2px;
  }
  .benefits li { height: 38.4px; line-height: 24px; }

  .site-footer {
    position: absolute; left: 535px; top: 782px;
    font-size: 12.5px; white-space: nowrap; color: var(--white);
  }
  .site-footer .label { color: var(--green); }
  .site-footer .year { margin-left: 14px; }
</style>
</head>
<body>
<div class="page">
  <div class="feature-art" role="img" aria-label="Large decorative brand numeral artwork in green and white"></div>

  <div class="brand"><span class="brand-dot"></span><span class="brand-name">TALLOWBROOK</span></div>

  <nav class="main-nav">
    <a href="#" style="left:377px;top:253px">HOME</a>
    <a href="#" style="left:340px;top:282px">THE STORY</a>
    <a href="#" style="left:260px;top:311px">WHY TALLOW-BROOK.COM</a>
    <a href="#" class="is-active" style="left:263px;top:341px">ARE YOU ELIGIBLE ?</a>
    <a href="#" style="left:296px;top:371px">MEMBERS</a>
    <a href="#" style="left:299px;top:401px">CLIENTS</a>
  </nav>

  <ul class="benefits">
    <li>36 %, NOT 390 - 600 %</li>
    <li>TRANSPARENT</li>
    <li>FEE FREE</li>
    <li>BILL PAID WITHIN 72 HRS</li>
    <li>PAYBACK STRUCTURE OVER 12 MONTHS</li>
  </ul>

  <footer class="site-footer"><span class="label">Copyright : </span>TALLOW-BROOK.COM<span class="year">2014</span></footer>
</div>
</body>
</html>
```